Probate (Legal) Wordpress Design with Coding for Online Company

I need a Wordpress design with coding, pictures, content to be provided by me, fully responsive, and development. This is for a 6-7 page design.

Pages Needed: Home/About/Probate/Process/FAQ/Contact Us/Blog.

The home page should be organized as followed:
-Steps in Probate: Gather; Implement; Close (each step will come with content)
-Flat-Fee Price & Savings: Content will go here with a button to contact us (phone number) or just the phone number.
-You Have Questions, We Have Answers: five questions with content. Only one question answer to show at a time when clicked on the question from the list.
-Get to Know Us: a brief description with content about what we do and who we are.

Main image slogan: Helping Californians deal with loss with DIGNITY & UNDERSTATING (you may use a better slogan if you wish).

The Contact page should not have a map since we are an online company. We service the entire state of California in every county and city.

The About page should be simple, direct, and easy on the eye. It should have a brief description of who we are and it should have no more than 6 reasons why the client should hire us.

About our online California company. We are not attorneys but legal document assistants who prepare legal documents for probate estate when someone dies with or without a will and assets need to be distributed. We have a flat-fee for Formal Probate of $999 and $699 for Informal Probate. We are an online company and offer our services to the entire state of California in every county. We do everything over the phone and email. The turn around time for us to prepare the initial legal paperwork for the client is within 3-5 business days. We can prepare, file, serve and manage a probate matter from petition to closing. We are not attorneys so our prices are very affordable compare to the attorney.

The company name for the website will be www.velmarhollow.com, The Velmar Hollow Group.

I do not have a logo yet. The colors of the website should be easy on the eye and calming. THE SITE SHOULD BE SIMPLE AND STRAIGHT TO THE POINT. EASY TO NAVIGATE.

The company phone number should be very visible and should stand out to the client. It should also be clickable and ready to dial for smartphone users.

I do not want a contact form on the homepage. THE MAIN THING IS FOR THE POTENTIAL CLIENT TO CALL OUR OFFICE TO SIGN UP.

I do like some images of family or people since we are dealing with people who just lost a loved one. Not all the images have to be of people.

The site should not look like we practice law or that people can mistake us for attorneys.

Target Market(s)

People who just lost a loved one who had property, assets, in California but died with or without a will or trust. This is for people looking to hire non-attorneys.

Coding

Coded - Design and coding required

Font styles to use
Serif

Colors

Designer to choose colors to be used in the design.

Requirements
Must have
• Refer to Project Description.
Nice to have
• The sample images provided is what I am attracted to for the homepage image.
Should not have

```html
<!DOCTYPE html>
<html lang="en">
<head>
<meta charset="utf-8">
<title>The Velmar Hollow Group – California Probate Document Assistance</title>
<link href="https://fonts.googleapis.com/css2?family=Open+Sans:wght@400;600;700;800&display=swap" rel="stylesheet">
<style>
:root{
  --blue:#1b8fd8;
  --blue-dark:#0c78c0;
  --blue-deep:#0a6aae;
  --ink:#2b2f33;
  --muted:#5b6168;
  --light:#eef0f3;
  --white:#ffffff;
}
*{margin:0;padding:0;box-sizing:border-box}
html,body{width:1200px;height:3041px;overflow:hidden}
body{position:relative;font-family:"Open Sans",Arial,sans-serif;color:var(--ink);background:var(--white)}
.abs{position:absolute}
a{color:inherit;text-decoration:none}

/* header */
.site-header{left:0;top:0;width:1200px;height:77px;background:var(--white)}
.brand{left:132px;top:22px;display:flex;align-items:center;gap:8px}
.brand-mark{width:26px;height:26px;background:var(--blue)}
.brand-name{font-size:19px;font-weight:600;color:var(--blue);white-space:nowrap}
.main-nav{left:340px;top:30px;display:flex;gap:24px;font-size:10.5px;font-weight:700;color:#333;text-transform:uppercase;white-space:nowrap}
.main-nav .active{color:var(--blue);border-bottom:2px solid var(--blue);padding-bottom:6px}
.call{left:898px;top:18px}
.call svg{position:absolute;left:0;top:8px}
.call-label{position:absolute;left:40px;top:0;font-size:10px;font-weight:700;color:#333;white-space:nowrap}
.call-number{position:absolute;left:38px;top:16px;background:var(--blue);color:#fff;font-size:19px;font-weight:700;padding:1px 10px;white-space:nowrap}

/* hero */
.hero{left:0;top:77px;width:1200px;height:549px;background:linear-gradient(180deg,#2d4d8c 0%,#3a5e9e 35%,#2a3f6c 65%,#8a5a3a 100%)}
.hero-band{left:274px;top:304px;width:648px;height:112px;background:rgba(10,20,40,.35)}
.hero-title{left:0;top:320px;width:1200px;text-align:center;color:#fff;font-size:29px;font-weight:700;line-height:44px;text-transform:uppercase}
.hero-dots{left:560px;top:580px;display:flex;gap:9px}
.hero-dots span{width:8px;height:8px;border-radius:50%;background:rgba(255,255,255,.6)}
.hero-dots span.on{background:#fff}

/* steps */
.steps-photo{left:180px;top:670px;width:340px;height:556px;background:linear-gradient(180deg,#e9d8c8 0%,#c9dbe9 55%,#3b4f72 100%);border-radius:120px 120px 0 0}
.section-title{font-size:24px;font-weight:700;color:var(--blue);text-transform:uppercase}
.rule{width:70px;height:2px;background:var(--blue)}
.steps-title{left:634px;top:680px}
.steps-rule{left:634px;top:716px}
.steps-intro{left:634px;top:744px;width:420px;font-size:13px;line-height:22px;color:var(--muted)}
.step{left:634px;width:440px;height:100px}
.step-icon{position:absolute;left:0;top:0;width:80px;height:80px;border-radius:50%;background:var(--blue)}
.step-icon svg{position:absolute;left:20px;top:20px}
.step h3{position:absolute;left:110px;top:0;font-size:15px;font-weight:700;color:var(--blue)}
.step p{position:absolute;left:110px;top:24px;width:300px;font-size:11px;line-height:16px;color:var(--muted)}

/* price */
.price{left:0;top:1226px;width:1200px;height:430px;background:linear-gradient(110deg,#1a84c9 0%,#2b95d6 45%,#1d8ad0 100%)}
.price-title{left:176px;top:1285px;color:#fff}
.price-rule{left:176px;top:1330px;background:#fff}
.price-text{left:176px;top:1370px;width:460px;font-size:13.5px;line-height:22px;color:#fff;text-align:justify}
.btn-contact{left:176px;top:1530px;width:142px;height:41px;background:#fff;color:var(--blue);font-size:13px;font-weight:700;text-transform:uppercase;display:flex;align-items:center;justify-content:center}
.savings-art{left:770px;top:1315px;width:220px;height:220px;border-radius:50%;background:rgba(255,255,255,.22)}

/* about */
.about{left:0;top:1656px;width:1200px;height:592px;background:var(--light)}
.about-title{left:176px;top:1710px}
.card{left:176px;width:454px;height:192px;background:#fff;box-shadow:0 2px 6px rgba(0,0,0,.06)}
.card svg{position:absolute;left:40px;top:40px}
.card h3{position:absolute;left:128px;top:34px;font-size:14px;font-weight:700;color:var(--blue);text-transform:uppercase}
.card p{position:absolute;left:128px;top:60px;width:300px;font-size:11px;line-height:17px;color:var(--muted)}
.team-photo{left:690px;top:1683px;width:330px;height:565px;background:linear-gradient(180deg,#dfe2e6 0%,#2e3640 40%,#1e2328 100%);border-radius:140px 140px 0 0}

/* faq */
.faq{left:0;top:2248px;width:1200px;height:503px;background:linear-gradient(180deg,#6fa6d6 0%,#9ec3e1 40%,#5c8ab2 62%,#b7a58c 100%)}
.faq-title{left:693px;top:2288px;color:var(--blue);font-size:24px;font-weight:700}
.faq-item{left:693px;width:349px;height:45px;background:#fff;font-size:13px;color:#333;display:flex;align-items:center;justify-content:space-between;padding:0 14px 0 16px}
.faq-item svg{flex:none}
.faq-answer{left:693px;top:2596px;width:349px;height:118px;background:#fff;padding:6px 16px;font-size:11px;line-height:16px;color:var(--muted);border-top:1px solid #e3e3e3}

/* footer */
.site-footer{left:0;top:2751px;width:1200px;height:253px;background:var(--blue)}
.foot-head{font-size:11px;font-weight:700;color:#fff;text-transform:uppercase}
.foot-line{font-size:11px;color:#fff;line-height:17px}
.foot-row{display:flex;gap:14px;align-items:flex-start}
.foot-menu{left:391px;top:2830px;font-size:11px;line-height:20px;color:#fff}
.email-field{left:594px;top:2832px;width:222px;height:42px;background:#fff;display:flex;align-items:center;gap:14px;padding-left:16px;font-size:12px;color:#555}
.btn-signup{left:597px;top:2893px;width:98px;height:38px;border:2px solid #fff;color:#fff;font-size:12px;font-weight:700;display:flex;align-items:center;justify-content:center;text-transform:uppercase}
.foot-brand{left:914px;top:2802px;display:flex;align-items:center;gap:8px}
.foot-brand .brand-mark{background:#fff}
.foot-brand .brand-name{color:#fff}
.social{left:914px;top:2903px;display:flex;gap:14px}
.social span{width:34px;height:34px;border-radius:50%;background:var(--blue-deep)}
.copyright{left:0;top:3004px;width:1200px;height:37px;background:var(--blue-dark);color:#dbeeff;font-size:10px;display:flex;align-items:center;justify-content:center}
</style>
</head>
<body>

<header class="abs site-header">
  <div class="abs brand"><span class="brand-mark"></span><span class="brand-name">Velmar Hollow</span></div>
  <nav class="abs main-nav">
    <a class="active" href="#">Home</a><a href="#">About</a><a href="#">Probate</a><a href="#">Process</a><a href="#">FAQ</a><a href="#">Contact Us</a><a href="#">Blog</a>
  </nav>
  <div class="abs call">
    <svg width="30" height="30" viewBox="0 0 24 24" fill="none" stroke="#1b8fd8" stroke-width="2"><path d="M5 3h4l2 5-2.5 1.5a11 11 0 0 0 6 6L16 13l5 2v4a2 2 0 0 1-2 2A16 16 0 0 1 3 5a2 2 0 0 1 2-2z"/></svg>
    <span class="call-label">CALL US NOW</span>
    <a class="call-number" href="tel:5552104477">555.210.4477</a>
  </div>
</header>

<section class="abs hero" role="img" aria-label="City skyline at dusk with lit towers and the bay"></section>
<div class="abs hero-band"></div>
<h1 class="abs hero-title">Helping Californians deal with loss<br>with dignity &amp; understating</h1>
<div class="abs hero-dots"><span></span><span class="on"></span><span></span><span></span></div>

<div class="abs steps-photo" role="img" aria-label="Smiling family of four standing together"></div>
<h2 class="abs section-title steps-title">Steps in Probate</h2>
<div class="abs rule steps-rule"></div>
<p class="abs steps-intro">We prepare your probate papers by phone and email, anywhere in California.</p>

<div class="abs step" style="top:833px">
  <div class="step-icon"><svg width="40" height="40" viewBox="0 0 40 40" fill="none" stroke="#fff" stroke-width="2.5"><path d="M14 6h14l6 6v22H14v-8"/><path d="M4 20h16M15 15l5 5-5 5"/></svg></div>
  <h3>GATHER</h3>
  <p>We collect the will, asset details and family information over the phone, then confirm every fact so nothing is missed before any form is filed.</p>
</div>
<div class="abs step" style="top:955px">
  <div class="step-icon"><svg width="40" height="40" viewBox="0 0 40 40" fill="none" stroke="#fff" stroke-width="2.5"><path d="M8 4h18l6 6v24H8z"/><path d="M13 14h14M13 20h14M13 26h6"/><circle cx="28" cy="30" r="6" fill="#fff"/><path d="M25 30l2 2 4-4" stroke="#1b8fd8"/></svg></div>
  <h3>IMPLEMENT</h3>
  <p>Your petition is prepared within 3–5 business days, filed with the county court and served to heirs, with updates sent at every stage.</p>
</div>
<div class="abs step" style="top:1077px">
  <div class="step-icon"><svg width="40" height="40" viewBox="0 0 40 40" fill="none" stroke="#fff" stroke-width="3"><path d="M6 6l10 10M16 8v8H8M34 6L24 16M24 8v8h8M6 34l10-10M16 32v-8H8M34 34L24 24M24 32v-8h8"/></svg></div>
  <h3>CLOSE</h3>
  <p>Once the court approves, we prepare the final accounting and distribution papers so assets reach the heirs and the estate is properly closed.</p>
</div>

<section class="abs price"></section>
<h2 class="abs section-title price-title">Flat-Fee Price &amp; Savings</h2>
<div class="abs rule price-rule"></div>
<p class="abs price-text">Because we are legal document assistants and not attorneys, our fees stay simple and low. Formal probate is a flat $999 and informal probate is a flat $699, with no hourly billing and no percentage of the estate. You know the full price before we begin, and every step is handled over the phone and by email.</p>
<a class="abs btn-contact" href="tel:5552104477">Contact Us</a>
<div class="abs savings-art" role="img" aria-label="White piggy bank with a coin, symbolising savings"></div>

<section class="abs about"></section>
<h2 class="abs section-title about-title">Get to Know Us</h2>
<div class="abs card" style="top:1790px">
  <svg width="56" height="70" viewBox="0 0 56 70" fill="none" stroke="#1b8fd8" stroke-width="3"><rect x="4" y="8" width="48" height="58"/><rect x="18" y="2" width="20" height="10" fill="#1b8fd8"/><path d="M12 26l4 4 6-6M12 42l4 4 6-6M28 28h16M28 44h16M12 56h32"/></svg>
  <h3>What we do</h3>
  <p>We prepare, file, serve and manage probate paperwork for families across every county in California, from the first petition to the final closing order, all by phone and email so you never need to leave home during a difficult time.</p>
</div>
<div class="abs card" style="top:1999px">
  <svg width="70" height="56" viewBox="0 0 70 56" fill="#1b8fd8"><circle cx="35" cy="10" r="8"/><rect x="25" y="20" width="20" height="12" rx="3"/><rect x="2" y="36" width="66" height="6"/><circle cx="12" cy="48" r="5"/><circle cx="35" cy="48" r="5"/><circle cx="58" cy="48" r="5"/></svg>
  <h3>Who we are</h3>
  <p>The Velmar Hollow Group is a team of registered legal document assistants. We are not attorneys, which keeps our prices affordable, and we guide each family with patience, clear answers and steady support through the whole process.</p>
</div>
<div class="abs team-photo" role="img" aria-label="Two smiling professionals in business attire"></div>

<section class="abs faq" role="img" aria-label="Family playing together on a beach at sunset"></section>
<h2 class="abs faq-title">FAQ</h2>
<div class="abs faq-item" style="top:2337px">1. How long does probate take in California?<svg width="10" height="12" viewBox="0 0 10 12"><path d="M2 1l5 5-5 5" fill="none" stroke="#555" stroke-width="1.6"/></svg></div>
<div class="abs faq-item" style="top:2390px">2. What does the flat fee include?<svg width="10" height="12" viewBox="0 0 10 12"><path d="M2 1l5 5-5 5" fill="none" stroke="#555" stroke-width="1.6"/></svg></div>
<div class="abs faq-item" style="top:2443px">3. Do I need an attorney for probate?<svg width="10" height="12" viewBox="0 0 10 12"><path d="M2 1l5 5-5 5" fill="none" stroke="#555" stroke-width="1.6"/></svg></div>
<div class="abs faq-item" style="top:2496px">4. Which counties do you serve?<svg width="10" height="12" viewBox="0 0 10 12"><path d="M2 1l5 5-5 5" fill="none" stroke="#555" stroke-width="1.6"/></svg></div>
<div class="abs faq-item" style="top:2549px">5. What happens if there is no will?<svg width="12" height="10" viewBox="0 0 12 10"><path d="M1 2l5 5 5-5" fill="none" stroke="#555" stroke-width="1.6"/></svg></div>
<p class="abs faq-answer">When someone dies without a will, California law decides who inherits. We prepare the petition to appoint an administrator and guide you through each court step until assets are distributed.</p>

<footer class="abs site-footer"></footer>
<div class="abs" style="left:132px;top:2794px">
  <div class="foot-head">Contact Us</div>
  <div class="foot-row" style="margin-top:22px"><svg width="10" height="14" viewBox="0 0 10 14" fill="#fff"><path d="M5 0a5 5 0 0 1 5 5c0 4-5 9-5 9S0 9 0 5a5 5 0 0 1 5-5z"/><circle cx="5" cy="5" r="2" fill="#1b8fd8"/></svg><span class="foot-line">2470 Alder Crest Lane<br>Fresno, California 93704</span></div>
  <div class="foot-row" style="margin-top:14px"><svg width="12" height="12" viewBox="0 0 24 24" fill="#fff"><path d="M5 3h4l2 5-2.5 1.5a11 11 0 0 0 6 6L16 13l5 2v4a2 2 0 0 1-2 2A16 16 0 0 1 3 5a2 2 0 0 1 2-2z"/></svg><a class="foot-line" href="tel:5552104477">555.210.4477</a></div>
  <div class="foot-row" style="margin-top:20px"><svg width="12" height="10" viewBox="0 0 12 10" fill="#fff"><rect width="12" height="10"/><path d="M0 0l6 5 6-5" fill="none" stroke="#1b8fd8"/></svg><span class="foot-line">info@velmarhollow.com</span></div>
</div>
<div class="abs foot-head" style="left:391px;top:2794px">Menu</div>
<div class="abs foot-menu">Home<br>About<br>Probate<br>Process<br>FAQ<br>Contact Us<br>Blog</div>
<div class="abs foot-head" style="left:594px;top:2794px">Newsletter Signup</div>
<div class="abs email-field"><svg width="14" height="11" viewBox="0 0 12 10" fill="#444"><rect width="12" height="10"/><path d="M0 0l6 5 6-5" fill="none" stroke="#fff"/></svg>E mail id</div>
<div class="abs btn-signup">Signup</div>
<div class="abs foot-brand"><span class="brand-mark"></span><span class="brand-name">Velmar Hollow</span></div>
<div class="abs foot-head" style="left:914px;top:2882px">Follow Us</div>
<div class="abs social"><span></span><span></span><span></span></div>
<div class="abs copyright">Copyright © 2017 All Rights Reserved</div>

</body>
</html>
```